Stationery Design Project for Nimbora, Chicago

Nimbora, a street parking application which helps car drivers find a street parking spot by offering an ideal path along which to look for parking. This path is calculated by our algorithm based on data (e.g. historical data, baseball games schedule, etc.). Along this path the driver will find a spot and will also save 70% of the search time. Customer we target is reg. between 21 and 45 yo.

We envision something young, fresh, bright and original. Slightly abstract maybe. It should represent the idea and elements of finding street parking in the city, e.g. car(s), parking spot, people, city, etc. (just ideas!).

Logo is attached.

Requirement:
- Business Cards (2 Sided Full Color CMYK)
- Letterhead (1 Sided Full Color CMYK)
- Envelope (1 Sided Full Color CMYK)
- Sticker (1 Sided Full Color CMYK), round with a 2inch diameter.

Reason: We're starting to get more and more designs and need more time to look into all of them. Very exciting!! Thanks to everybody!

Hi all, we're in the process of selecting our favs. Though choices!!! Really good submissions. Will keep you posted and sorry for the delay.

Target Market(s)

Car drivers and owners between 21 and 45

Industry/Entity Type

Parking

Requirements
Must have
• Sticker should be round and include company URL nimbora.com and the new logo which we will attach soon.
Should not have
• Should not be too serious or boring.

```html
<!DOCTYPE html>
<html lang="en">
<head>
<meta charset="utf-8">
<title>Nimbora Business Card – Front and Back</title>
<link rel="stylesheet" href="https://fonts.googleapis.com/css2?family=Open+Sans:wght@400;600;700&display=swap">
<style>
  :root {
    --backdrop: #e4e6e9;
    --card: #ffffff;
    --ink: #4a4a4a;
    --ink-strong: #2b2b2b;
    --brand-deep: #1b2f94;
    --brand-mid: #1f5fc0;
    --brand-light: #1ba9e1;
    --swoosh-dark: #111111;
    --swoosh-light: #bdbdbd;
    --on-brand: #ffffff;
  }
  * { margin: 0; padding: 0; box-sizing: border-box; }
  html, body {
    width: 954px;
    height: 1200px;
    overflow: hidden;
    background: var(--backdrop);
    font-family: "Open Sans", Arial, sans-serif;
  }
  .sheet { position: relative; width: 954px; height: 1200px; }
  .card {
    position: absolute;
    left: 78px;
    width: 798px;
    height: 454px;
    background: var(--card);
    overflow: hidden;
    box-shadow: 0 2px 8px rgba(0,0,0,0.18);
  }
  .card--front { top: 97px; }
  .card--back { top: 625px; }
  .card__wave { position: absolute; inset: 0; width: 100%; height: 100%; }
  .brand { position: absolute; display: flex; align-items: center; }
  .brand__dot {
    border-radius: 50%;
    background: var(--brand-mid);
    flex: none;
  }
  .brand__name {
    font-weight: 600;
    color: var(--ink-strong);
    letter-spacing: 1px;
    line-height: 1;
  }
  .card--front .brand { left: 52px; top: 45px; gap: 40px; }
  .card--front .brand__dot { width: 156px; height: 156px; }
  .card--front .brand__name { font-size: 76px; }
  .card--back .brand { left: 58px; top: 40px; gap: 42px; }
  .card--back .brand__dot { width: 166px; height: 166px; }
  .card--back .brand__name { font-size: 84px; }
  .contact {
    position: absolute;
    left: 88px;
    top: 238px;
    color: var(--ink);
    font-size: 21px;
    line-height: 37px;
  }
  .contact__label { font-weight: 700; }
  .contact__sep { margin: 0 8px; }
  .address {
    position: absolute;
    left: 88px;
    top: 323px;
    color: var(--ink);
    font-size: 21px;
    line-height: 30px;
  }
  .person {
    position: absolute;
    right: 22px;
    top: 371px;
    text-align: right;
    color: var(--on-brand);
    font-weight: 700;
  }
  .person__name { font-size: 23px; line-height: 30px; }
  .person__role { font-size: 18px; line-height: 24px; }
  .web {
    position: absolute;
    right: 26px;
    top: 404px;
    color: var(--on-brand);
    font-size: 20px;
  }
  .web__label { font-weight: 700; }
</style>
</head>
<body>
<main class="sheet">

  <section class="card card--front" aria-label="Business card front">
    <svg class="card__wave" viewBox="0 0 798 454" aria-hidden="true">
      <defs>
        <linearGradient id="band-front" x1="0" y1="0" x2="1" y2="0">
          <stop offset="0" stop-color="var(--brand-deep)"/>
          <stop offset="0.45" stop-color="var(--brand-light)"/>
          <stop offset="1" stop-color="var(--brand-deep)"/>
        </linearGradient>
        <linearGradient id="swoosh-front" x1="0" y1="0" x2="1" y2="0">
          <stop offset="0" stop-color="var(--swoosh-light)"/>
          <stop offset="0.35" stop-color="var(--swoosh-dark)"/>
          <stop offset="1" stop-color="var(--swoosh-dark)"/>
        </linearGradient>
      </defs>
      <path d="M0,398 C160,440 470,405 798,276 L798,454 L0,454 Z" fill="url(#band-front)"/>
      <path d="M140,428 C420,424 610,340 798,252 L798,266 C610,352 420,428 140,428 Z" fill="url(#swoosh-front)"/>
    </svg>

    <div class="brand">
      <span class="brand__dot"></span>
      <span class="brand__name">Nimbora</span>
    </div>

    <div class="contact">
      <p><span class="contact__label">t</span> : 123-456-7890<span class="contact__sep">|</span><span class="contact__label">c</span> : 123-456-7890</p>
      <p><span class="contact__label">e</span> : name@website.com<span class="contact__sep">|</span><span class="contact__label">w</span> : www.website.com</p>
    </div>

    <address class="address" style="font-style: normal;">
      City Name, Street Name<br>
      State Name, Country Code
    </address>

    <div class="person">
      <p class="person__name">Your Name</p>
      <p class="person__role">Designation</p>
    </div>
  </section>

  <section class="card card--back" aria-label="Business card back">
    <svg class="card__wave" viewBox="0 0 798 454" aria-hidden="true">
      <defs>
        <linearGradient id="band-back" x1="0" y1="0" x2="1" y2="0">
          <stop offset="0" stop-color="var(--brand-deep)"/>
          <stop offset="0.45" stop-color="var(--brand-light)"/>
          <stop offset="1" stop-color="var(--brand-deep)"/>
        </linearGradient>
        <linearGradient id="swoosh-back" x1="0" y1="0" x2="1" y2="0">
          <stop offset="0" stop-color="var(--swoosh-light)"/>
          <stop offset="0.35" stop-color="var(--swoosh-dark)"/>
          <stop offset="1" stop-color="var(--swoosh-dark)"/>
        </linearGradient>
      </defs>
      <path d="M0,398 C160,440 470,405 798,276 L798,454 L0,454 Z" fill="url(#band-back)"/>
      <path d="M140,428 C420,424 610,340 798,252 L798,266 C610,352 420,428 140,428 Z" fill="url(#swoosh-back)"/>
    </svg>

    <div class="brand">
      <span class="brand__dot"></span>
      <span class="brand__name">Nimbora</span>
    </div>

    <p class="web"><span class="web__label">w</span> : www.website.com</p>
  </section>

</main>
</body>
</html>
```